WeatheredOnward.net wordpress design

Concept: Website where personal stories, personal videos can be posted as a challenge while awaiting the wisdom of experience from others who have survived this same event or challenge in their lifetime.
Support aspects will be in 4 quadrants of Challenges:
1. Financial 2. Medical & Physical
3. Legal Matters 4. Psychological & Spiritual - ability to chat online with a spiritual/psychological counselor or life coach
Updates
Project Deadline Extended
Reason: Bit more time to complete designs.
Wanted to thank all of you for your designs! Greatly appreciated. Very creative ideas that captured the essence of this website. Will be back with a selection very shortly.
Target Market(s)
Anyone looking for a solution based upon experiential wisdom
Industry/Entity Type
Financial
Requirements
Must have
- Interactive website: Where you can post a challenge or issue via a written question or a video and ask for a solution.
Ability to access any of the 4 Quadrants (as listed above) to ask for an expert, via experience, advice and wisdom from those who have similar challenges.

```html
<!DOCTYPE html>
<html lang="en">
<head>
<meta charset="utf-8">
<title>WeatheredOnward.net</title>
<link rel="stylesheet" href="https://fonts.googleapis.com/css2?family=Mulish:wght@400;600;700;800&display=swap">
<style>
:root{
  --orange:#f5a623;
  --orange-text:#d9901a;
  --dark:#1c1c1c;
  --ink:#222;
  --muted:#777;
  --line:#ccc;
  --field:#999;
  --panel:#fff;
  --pale:#e4e4e4;
  --pill:#8a8a8a;
}
*{box-sizing:border-box;margin:0;padding:0}
html,body{width:1063px;height:1200px;overflow:hidden}
body{position:relative;font-family:"Mulish",sans-serif;color:var(--ink);
  background:var(--pale) radial-gradient(#d6d6d6 1px,transparent 1.2px) 0 0/4px 4px}
.hero{position:absolute;left:0;top:0;width:1063px;height:442px;
  background:repeating-linear-gradient(45deg,#161616 0 2px,#1e1e1e 2px 4px)}
.hero::before{content:"";position:absolute;left:0;top:0;width:100%;height:3px;background:var(--orange)}
.nav{position:absolute;left:126px;top:3px;width:841px;height:27px;background:var(--panel);
  border-radius:0 0 3px 3px;font-size:13px}
.nav a{position:absolute;top:5px;color:#444;text-decoration:none}
.nav .sep{position:absolute;top:5px;width:1px;height:18px;background:var(--line)}
.nav .home{font-weight:700;color:var(--ink)}
.nav .auth{font-size:9.5px;font-weight:700;text-decoration:underline;top:7px;color:var(--ink)}
.search{position:absolute;left:683px;top:5px;width:152px;height:18px;border:1px solid var(--field);
  font-size:10px;color:#aaa;font-style:italic;padding:2px 4px}
.search b{position:absolute;right:0;top:0;width:22px;height:16px;background:var(--dark);color:#fff;
  font-style:normal;font-size:10px;text-align:center;line-height:16px}
.logo{position:absolute;left:126px;top:58px;width:161px;height:73px;background:var(--panel);
  border-radius:3px;display:flex;align-items:center;gap:9px;padding:0 8px}
.logo .mark{width:34px;height:34px;background:var(--orange);flex:none}
.logo .name{font-size:15px;font-weight:800;color:var(--orange);line-height:1.1}
.portrait{position:absolute;left:290px;top:30px;width:445px;height:394px;
  background:radial-gradient(ellipse 45% 55% at 45% 45%,#b88a74,#5a5050 60%,#2a2a2a 85%,transparent 100%)}
.dots{position:absolute;left:127px;top:389px;display:flex;gap:5px}
.dots i{width:8px;height:8px;border-radius:50%;background:#ddd}
.dots i:first-child{background:var(--orange);box-shadow:0 0 0 1px #fff}
.slogan{position:absolute;left:490px;top:358px;color:#fff}
.slogan h2{font-size:21px;font-weight:400}
.slogan h2 b{font-weight:800}
.slogan p{font-size:11.5px}
.ask{position:absolute;left:725px;top:58px;width:242px;height:338px;background:var(--panel);border-radius:3px}
.ask h3{position:absolute;left:11px;top:27px;font-size:19px;font-weight:400;color:#444}
.ask .lead{position:absolute;left:11px;top:56px;width:228px;font-size:11.5px;color:var(--muted);line-height:1.2}
.field{position:absolute;left:10px;width:222px;height:24px;border:1px solid var(--line);border-radius:3px;
  font-size:11.5px;color:#aaa;padding:4px 6px}
.btn-dark{position:absolute;background:var(--dark);color:#fff;font-weight:700;font-size:11.5px;
  text-align:center;border-radius:3px;line-height:22px;height:23px}
.content{position:absolute;left:126px;top:424px;width:841px;height:642px;background:var(--panel);border-radius:3px}
.section-title{position:absolute;top:12px;font-size:18px;font-weight:400;color:#333}
.divider{position:absolute;height:8px;background:radial-gradient(ellipse 50% 100% at 50% 0,#dcdcdc,transparent)}
.article{position:absolute;left:16px;width:380px}
.article h4{font-size:13.5px;font-weight:700}
.article .meta{font-size:9.5px;font-weight:700;color:var(--orange-text);line-height:1.2}
.share{display:flex;gap:2px;margin:4px 0 5px}
.share i{width:14px;height:14px;border-radius:2px}
.article p{font-size:11px;color:var(--muted);line-height:1.2}
.pill{display:inline-block;background:var(--pill);color:#fff;font-size:10.5px;border-radius:6px;
  padding:0 8px;line-height:14px;margin-top:2px;border:1px solid #777}
.quad{position:absolute;width:170px}
.quad h5{font-size:15px;font-weight:700;line-height:1.2;margin-bottom:10px}
.quad .item{font-size:10.5px;color:var(--muted);line-height:1.25;margin-bottom:8px}
.quad .item b{color:#444;font-weight:700}
.chat{position:absolute;left:482px;top:510px}
.chat h3{font-size:19px;font-weight:400;color:#333;line-height:1.25}
.chat p{font-size:11.5px;color:var(--muted);margin-top:8px;line-height:1.2}
</style>
</head>
<body>
<div class="hero">
  <nav class="nav">
    <a class="home" style="left:18px">Home</a><span class="sep" style="left:73px"></span>
    <a style="left:100px">Profile</a><span class="sep" style="left:162px"></span>
    <a style="left:183px">Followers</a><span class="sep" style="left:266px"></span>
    <a style="left:290px">My Uploads</a>
    <a class="auth" style="left:576px">Login</a>
    <span style="position:absolute;left:614px;top:6px;font-size:10px;color:#666">|</span>
    <a class="auth" style="left:630px">Register</a>
    <div class="search">search<b>Go</b></div>
  </nav>
  <div class="logo"><span class="mark"></span><div class="name">Weathered<br>Onward.net</div></div>
  <div class="portrait" role="img" aria-label="Portrait of a smiling older man in a suit"></div>
  <div class="dots"><i></i><i></i><i></i><i></i><i></i></div>
  <div class="slogan"><h2>Learn from <b>Experience</b></h2><p>Experience is the best teacher overall</p></div>
  <form class="ask">
    <h3>Ask your Question</h3>
    <p class="lead">and get answered by the experienced people around the world</p>
    <div class="field" style="top:101px">Name</div>
    <div class="field" style="top:128px">email address</div>
    <div class="field" style="top:156px;height:92px">your question</div>
    <div class="field" style="top:251px">Select Quadrant</div>
    <div class="field" style="top:279px;width:159px">Upload Video (optional)</div>
    <div class="field" style="top:279px;left:168px;width:64px;background:#f3f3f3;text-align:center">Browse</div>
    <div class="btn-dark" style="left:11px;top:306px;width:221px">Get Answer</div>
  </form>
</div>

<main class="content">
  <h2 class="section-title" style="left:14px">Fresh Articles</h2>
  <h2 class="section-title" style="left:484px">Browse by Quadrant</h2>
  <div class="divider" style="left:60px;top:46px;width:740px"></div>

  <article class="article" style="top:65px">
    <h4>Problem in life with Money</h4><div class="meta">July 13, 2012<br>132 response, 8996 views</div>
    <div class="share"><i style="background:#f08a24"></i><i style="background:#f5a623"></i><i style="background:#3b5998"></i><i style="background:#9cc3e6"></i><i style="background:#4fb5e6"></i><i style="background:#e84a9b"></i></div>
    <p>This is Pixelform's version of Lorem Ipsum. Proin gravida nibh vel velit auctor aliquet. Aenean sollicitudin, lorem quis bibendum auctor, nisi elit consequat ipsum, nec sagittis sem nibh id elit. Duis sed ...</p>
    <span class="pill">more</span>
  </article>
  <article class="article" style="top:208px">
    <h4>Problem in life with Money</h4><div class="meta">July 13, 2012<br>132 response, 8996 views</div>
    <div class="share"><i style="background:#f08a24"></i><i style="background:#f5a623"></i><i style="background:#3b5998"></i><i style="background:#9cc3e6"></i><i style="background:#4fb5e6"></i><i style="background:#e84a9b"></i></div>
    <p>This is Pixelform's version of Lorem Ipsum. Proin gravida nibh vel velit auctor aliquet. Aenean sollicitudin, lorem quis bibendum auctor, nisi elit consequat ipsum, nec sagittis sem nibh id elit. Duis sed ...</p>
    <span class="pill">more</span>
  </article>
  <article class="article" style="top:350px">
    <h4>Problem in life with Money</h4><div class="meta">July 13, 2012<br>132 response, 8996 views</div>
    <div class="share"><i style="background:#f08a24"></i><i style="background:#f5a623"></i><i style="background:#3b5998"></i><i style="background:#9cc3e6"></i><i style="background:#4fb5e6"></i><i style="background:#e84a9b"></i></div>
    <p>This is Pixelform's version of Lorem Ipsum. Proin gravida nibh vel velit auctor aliquet. Aenean sollicitudin, lorem quis bibendum auctor, nisi elit consequat ipsum, nec sagittis sem nibh id elit. Duis sed ...</p>
    <span class="pill">more</span>
  </article>
  <article class="article" style="top:493px">
    <h4>Problem in life with Money</h4><div class="meta">July 13, 2012<br>132 response, 8996 views</div>
    <div class="share"><i style="background:#f08a24"></i><i style="background:#f5a623"></i><i style="background:#3b5998"></i><i style="background:#9cc3e6"></i><i style="background:#4fb5e6"></i><i style="background:#e84a9b"></i></div>
    <p>This is Pixelform's version of Lorem Ipsum. Proin gravida nibh vel velit auctor aliquet. Aenean sollicitudin, lorem quis bibendum auctor, nisi elit consequat ipsum, nec sagittis sem nibh id elit. Duis sed ...</p>
    <span class="pill">more</span>
  </article>

  <section class="quad" style="left:483px;top:70px">
    <h5>Financial Problems</h5>
    <div class="item"><b>Problem in life with Money</b><br>July 13, 2012<br>132 response, 8996 views</div>
    <div class="item"><b>Problem in life with Money</b><br>July 13, 2012<br>132 response, 8996 views</div>
    <div class="item"><b>Problem in life with Money</b><br>July 13, 2012<br>132 response, 8996 views</div>
    <span class="pill">more</span>
  </section>
  <section class="quad" style="left:671px;top:70px">
    <h5>Legal Matters</h5>
    <div class="item"><b>Problem in life with Money</b><br>July 13, 2012<br>132 response, 8996 views</div>
    <div class="item"><b>Problem in life with Money</b><br>July 13, 2012<br>132 response, 8996 views</div>
    <div class="item"><b>Problem in life with Money</b><br>July 13, 2012<br>132 response, 8996 views</div>
    <span class="pill">more</span>
  </section>
  <section class="quad" style="left:483px;top:290px">
    <h5>Medical &amp; Physical</h5>
    <div class="item"><b>Problem in life with Money</b><br>July 13, 2012<br>132 response, 8996 views</div>
    <div class="item"><b>Problem in life with Money</b><br>July 13, 2012<br>132 response, 8996 views</div>
    <div class="item"><b>Problem in life with Money</b><br>July 13, 2012<br>132 response, 8996 views</div>
    <span class="pill">more</span>
  </section>
  <section class="quad" style="left:671px;top:290px">
    <h5>Psychological &amp;<br>Spiritual</h5>
    <div class="item"><b>Problem in life with Money</b><br>July 13, 2012<br>132 response, 8996 views</div>
    <div class="item"><b>Problem in life with Money</b><br>July 13, 2012<br>132 response, 8996 views</div>
    <span class="pill">more</span>
  </section>

  <div class="divider" style="left:500px;top:496px;width:340px"></div>
  <section class="chat">
    <h3>Chat Online with a<br>Life Coach</h3>
    <p>and get answered by the experienced<br>people around the world</p>
  </section>
  <div class="btn-dark" style="left:482px;top:600px;width:221px">Start Now</div>
</main>
</body>
</html>
```